HOT TUB - SPAS service needs an business card

I need an business for my company who his specialise in a maintenance,water treatment and cleaning of Hot Tub - Spas for commercial and residential customers. The company operate mainly in the ski resort of Chamonix, Megève and St Gervais. The final product should communicate pure water, cleanest and professional for luxury property's.
I have upload a logo but any improvement on it is welcome.(color,size, details etc..) or any other idea. Thank you
Company Name: 58 BAINS
My name: Lucien Marchetti
Email: lucimarch@examplemail.net
Tel: +33 (0)6 71 58 29 64
Description to be on the card in french(first langage) and in English:
- Spas service
- Entretien, traitement eau, nettoyage.
- Maintenance, water treatment, cleaning.
Industry/Entity Type
Residential
Colors
Designer to choose colors to be used in the design.
Look and feel
Each slider illustrates characteristics of the customer's brand and the style your logo design should communicate.

```html
<!DOCTYPE html>
<html lang="fr">
<head>
<meta charset="utf-8">
<title>58 BAINS – Cartes de visite</title>
<link rel="stylesheet" href="https://fonts.googleapis.com/css2?family=Source+Sans+3:wght@400;600;700&display=swap">
<style>
  :root {
    --page-bg: #ebe7e1;
    --card-blue: #28a5f5;
    --wave-mid: #1f80e2;
    --wave-deep: #0d5ecf;
    --wave-pale: #9fd2fb;
    --wave-mist: #d6ecfd;
    --art-tint: #4db5f7;
    --ink-light: #ffffff;
    --divider: rgba(255, 255, 255, 0.55);
  }
  * { box-sizing: border-box; margin: 0; padding: 0; }
  html, body {
    width: 1200px;
    height: 1148px;
    overflow: hidden;
    background: var(--page-bg);
    font-family: "Source Sans 3", "Myriad Pro", Arial, sans-serif;
    color: var(--ink-light);
  }
  .canvas { position: relative; width: 1200px; height: 1148px; }

  .card {
    position: absolute;
    width: 885px;
    height: 503px;
    border-radius: 26px;
    background: var(--card-blue);
    overflow: hidden;
    box-shadow: 0 3px 10px rgba(0, 0, 0, 0.18);
  }
  .card--front { left: 32px; top: 34px; }
  .card--back  { left: 249px; top: 573px; }

  .logo-art {
    position: absolute;
    background: linear-gradient(180deg, var(--art-tint), var(--card-blue));
    border-radius: 6px;
  }
  .card--front .logo-art { left: 162px; top: 49px; width: 562px; height: 153px; }
  .card--back  .logo-art { left: 109px; top: 94px; width: 680px; height: 188px; }

  .holder-name {
    position: absolute;
    left: 83px;
    top: 290px;
    font-size: 28px;
    font-weight: 700;
    line-height: 40px;
  }
  .contact-divider {
    position: absolute;
    left: 389px;
    top: 269px;
    width: 1.5px;
    height: 80px;
    background: var(--divider);
  }
  .contact-list {
    position: absolute;
    left: 413px;
    top: 268px;
    list-style: none;
    font-size: 27px;
    line-height: 47px;
  }
  .contact-list li { display: flex; align-items: center; gap: 12px; }
  .contact-icon { width: 26px; height: 26px; flex: none; }

  .waves { position: absolute; left: 0; top: 0; width: 885px; height: 503px; }

  .company-name {
    position: absolute;
    left: 624px;
    top: 434px;
    font-size: 37px;
    font-weight: 700;
    line-height: 46px;
    letter-spacing: 0.5px;
  }

  .services {
    position: absolute;
    left: 0;
    top: 350px;
    width: 100%;
    text-align: center;
  }
  .services-title {
    font-size: 31px;
    font-weight: 700;
    line-height: 40px;
    margin-bottom: 8px;
  }
  .services-line {
    font-size: 31px;
    font-weight: 400;
    line-height: 42px;
    word-spacing: 1px;
  }
  .services-line span + span { margin-left: 14px; }
</style>
</head>
<body>
<main class="canvas">

  <section class="card card--front" aria-label="Recto de la carte">
    <div class="logo-art" role="img" aria-label="Logo 58 BAINS : dessin au trait d'une montagne, d'un chalet et d'un spa"></div>

    <svg class="waves" viewBox="0 0 885 503" aria-hidden="true">
      <path d="M0 408 C 300 352 560 330 885 418 L885 503 L0 503 Z" fill="var(--wave-mid)"/>
      <path d="M0 428 C 300 372 560 350 885 432 L885 503 L0 503 Z" fill="var(--wave-deep)"/>
      <path d="M0 442 C 200 432 420 418 560 388 C 420 452 250 492 0 503 Z" fill="var(--wave-pale)"/>
      <path d="M0 468 C 200 468 390 446 560 392 C 400 470 200 503 0 503 Z" fill="var(--wave-mist)"/>
    </svg>

    <h1 class="holder-name">Lucien Marchetti</h1>
    <div class="contact-divider"></div>
    <ul class="contact-list">
      <li>
        <svg class="contact-icon" viewBox="0 0 24 24" aria-hidden="true">
          <circle cx="12" cy="12" r="10.5" fill="none" stroke="#fff" stroke-width="1.6"/>
          <path d="M8.3 6.6l1.8-.4 1.1 2.6-1.2 1c.6 1.4 1.6 2.5 3 3.2l1-1.2 2.6 1.1-.4 1.8c-.2.6-.8.9-1.4.8-3.7-.6-6.6-3.5-7.2-7.2-.1-.6.2-1.2.7-1.7z" fill="#fff"/>
        </svg>
        <span>+33 (0)6 71 58 29 64</span>
      </li>
      <li>
        <svg class="contact-icon" viewBox="0 0 24 24" aria-hidden="true">
          <rect x="2" y="6" width="20" height="13" rx="1.5" fill="#fff"/>
          <path d="M2.8 7l9.2 7 9.2-7" fill="none" stroke="var(--card-blue)" stroke-width="1.6"/>
        </svg>
        <span>lucimarch@examplemail.net</span>
      </li>
    </ul>

    <p class="company-name">58 BAINS</p>
  </section>

  <section class="card card--back" aria-label="Verso de la carte">
    <div class="logo-art" role="img" aria-label="Logo 58 BAINS : dessin au trait d'une montagne, d'un chalet et d'un spa"></div>

    <div class="services">
      <h2 class="services-title">SPAS SERVICES</h2>
      <p class="services-line"><span>•Entretien</span><span>• traitement eau</span><span>• nettoyage</span></p>
      <p class="services-line" lang="en"><span>•Maintenance</span><span>• water treatment</span><span>•cleaning.</span></p>
    </div>
  </section>

</main>
</body>
</html>
```